Biz Card Design TVCP

New business card for a new company.
Logo was completed by a designer on ArtHarbor and looking to continue requesting additional services.
Company Name: Tidal Vector Power Consulting
Although this company is starting in Canada, we will be moving towards a global presence within the next 6 months.
Key elements to this business are as follows.
Energy Procurement
Energy Reduction Services
Demand Side Consulting
Energy Efficiency Consulting
Saving Clients Money
Helping Them Go "Green"
Managing Their Energy Requirements
Basically the goal for our company is to find the best procurement solution for our clients and reduce their energy consumption. This reduces their expenses and the amount of greenhouse gas they produce on a daily basis.
I have been in the energy footprint for the last 20 years and know that most companies are looking to "do whatever is necessary to get them to sign on the dotted line". I would prefer to walk away from a client that I can't help than to put them into a situation that they will regret for years to come. This is where the "TIDAL" part of the company name comes from.
The following is a catch phrase that encompasses what we do.
"Reducing your carbon footprint & energy bill at the same time!"
The back of the card needs to have this statement along with some sort of illustration. The back is a playground for creative ideas.
The front of the card needs the following.
Logo.
First & Last Name (Gus Marwick)
Title (Energy Warrior)
Phone Number (555) 314-2718
Fax Number (555) 271-8314
Email Address gus@tidalvectorpowerconsulting.example
Address 47 fenwick rd Toronto Ontario K4T 2P9
I want it to be a card that is remembered when any of my staff give it to a customer. It HAS to stand out.
Target Market(s)
Business Owners, Decision Makers, 30 to 65+
Industry/Entity Type
Business
Look and feel

```html
<!DOCTYPE html>
<html lang="en">
<head>
<meta charset="utf-8">
<title>Tidal Vector Power Consulting – Business Card</title>
<link href="https://fonts.googleapis.com/css2?family=Open+Sans:wght@400;600;700&display=swap" rel="stylesheet">
<style>
  :root {
    --page-bg: #ecebe8;
    --card-black: #121212;
    --card-black-soft: #262626;
    --card-white: #ffffff;
    --brand-green: #1e9e45;
    --brand-green-light: #8cc86a;
    --brand-green-dark: #0f7a34;
    --brand-blue: #3f6fbf;
    --ink: #2b2b2b;
    --tagline-light: #f2f2f2;
  }
  * { box-sizing: border-box; margin: 0; padding: 0; }
  html, body { width: 1200px; height: 900px; overflow: hidden; }
  body {
    background: var(--page-bg);
    font-family: "Open Sans", Arial, sans-serif;
    position: relative;
  }
  .card {
    position: absolute;
    left: 250px;
    width: 700px;
    height: 400px;
    border-radius: 26px;
    overflow: hidden;
    box-shadow: 0 6px 18px rgba(0,0,0,.22);
  }
  .card--back { top: 36px; background: var(--card-black); }
  .card--front { top: 464px; background: var(--card-white); }

  /* Back side */
  .back-texture {
    position: absolute; inset: 0;
    background: radial-gradient(ellipse at 60% 30%, var(--card-black-soft) 0%, var(--card-black) 70%);
  }
  .back-wordmark {
    position: absolute; left: 0; right: 0; top: 150px;
    text-align: center;
    font-weight: 700; font-size: 38px; letter-spacing: -0.5px;
    color: var(--brand-green);
  }
  .back-tagline {
    position: absolute; left: 0; right: 0; top: 232px;
    text-align: center;
    font-size: 17px; color: var(--tagline-light);
  }

  /* Front side */
  .front-art { position: absolute; inset: 0; width: 700px; height: 400px; }
  .front-wordmark {
    position: absolute; left: 34px; top: 110px;
    font-weight: 700; font-size: 21px; letter-spacing: -0.4px;
    color: var(--brand-green);
  }
  .contact-block {
    position: absolute; right: 40px; top: 96px;
    text-align: right;
  }
  .contact-name { font-size: 24px; font-weight: 700; color: var(--brand-green); line-height: 1.1; }
  .contact-title { font-size: 14px; font-weight: 700; color: var(--brand-blue); margin-bottom: 6px; padding-right: 22px; }
  .contact-line {
    font-size: 14px; color: var(--ink); line-height: 24px;
    display: flex; justify-content: flex-end; align-items: center; gap: 8px;
  }
  .contact-line svg { width: 14px; height: 14px; flex: none; }
  .contact-address {
    position: absolute; left: 40px; top: 296px;
    font-size: 17px; color: var(--ink); line-height: 26px;
  }
  .addr-line { display: flex; align-items: center; gap: 8px; }
  .addr-line svg { width: 16px; height: 16px; flex: none; }
  .addr-indent { padding-left: 24px; }
  .front-tagline {
    position: absolute; left: 40px; top: 354px;
    font-size: 18px; color: var(--ink);
  }
</style>
</head>
<body>

  <section class="card card--back" aria-label="Card back">
    <div class="back-texture" role="img" aria-label="Faint repeating dollar-sign pattern on black"></div>
    <div class="back-wordmark">Tidal Vector Power Consulting</div>
    <p class="back-tagline">"Reducing your carbon footprint &amp; energy bill at the same time!"</p>
  </section>

  <section class="card card--front" aria-label="Card front">
    <svg class="front-art" viewBox="0 0 700 400" aria-hidden="true">
      <path d="M0,0 H520 C440,140 290,225 0,250 Z" fill="var(--card-black)"/>
      <path d="M520,-10 C440,140 290,225 -10,250" transform="translate(6,6)" fill="none" stroke="var(--brand-green-dark)" stroke-width="8"/>
      <path d="M520,-10 C440,140 290,225 -10,250" transform="translate(15,14)" fill="none" stroke="var(--brand-green-light)" stroke-width="5"/>
      <path d="M520,-10 C440,140 290,225 -10,250" transform="translate(23,21)" fill="none" stroke="var(--brand-green)" stroke-width="5"/>
      <path d="M520,-10 C440,140 290,225 -10,250" transform="translate(31,28)" fill="none" stroke="var(--brand-blue)" stroke-width="4"/>
    </svg>

    <div class="front-wordmark">Tidal Vector Power Consulting</div>

    <div class="contact-block">
      <div class="contact-name">Gus Marwick</div>
      <div class="contact-title">Energy Warrior</div>
      <div class="contact-line">(555) 314-2718
        <svg viewBox="0 0 14 14" aria-hidden="true"><path d="M3 1l2.5 2.5-1.4 1.6c.8 1.8 2 3 3.8 3.8l1.6-1.4L13 10l-1.8 2.3C6 12 2 8 1.7 2.8z" fill="var(--brand-green)"/></svg>
      </div>
      <div class="contact-line">(555) 271-8314
        <svg viewBox="0 0 14 14" aria-hidden="true"><rect x="2" y="1" width="10" height="12" rx="1" fill="var(--brand-green)"/><rect x="4" y="4" width="6" height="1.5" fill="#fff"/><rect x="4" y="7" width="6" height="1.5" fill="#fff"/></svg>
      </div>
      <div class="contact-line">gus@tidalvectorpowerconsulting.example
        <svg viewBox="0 0 14 14" aria-hidden="true"><rect x="1" y="3" width="12" height="8" rx="1" fill="var(--brand-green)"/><path d="M1.5 3.5L7 8l5.5-4.5" fill="none" stroke="#fff" stroke-width="1.3"/></svg>
      </div>
    </div>

    <div class="contact-address">
      <div class="addr-line">
        <svg viewBox="0 0 16 16" aria-hidden="true"><path d="M8 1L1 8h2v7h4v-4h2v4h4V8h2z" fill="var(--brand-green)"/></svg>
        <span>47 fenwick rd Toronto</span>
      </div>
      <div class="addr-indent">Canada K4T 2P9</div>
    </div>

    <p class="front-tagline">"Reducing your carbon footprint &amp; energy bill at the same time!"</p>
  </section>

</body>
</html>
```